Marwick Law Letterhead

We need a new letterhead design for a Law Firm. The address for the law firm is 1475 Calloway Street, Suite 210, Houston, Texas 77041. Phone Number: 832-361-9027; Fax Number: 832-614-7359. The logo is uploaded to the project.

```html
<!DOCTYPE html>
<html lang="en">
<head>
<meta charset="utf-8">
<title>Marwick Law Letterhead</title>
<link rel="stylesheet" href="https://fonts.googleapis.com/css2?family=Montserrat:wght@400;500;600&display=swap">
<style>
  :root {
    --backdrop: #e8e8e9;
    --paper: #ffffff;
    --navy: #13295a;
    --navy-deep: #0e2150;
    --red: #e1232b;
    --red-deep: #8e1519;
    --blue: #3f5fae;
    --plum: #7a3569;
    --ink: #2a2a2a;
    --sign-tone: #ececee;
  }
  * { margin: 0; padding: 0; box-sizing: border-box; }
  html, body {
    width: 1200px; height: 874px; overflow: hidden;
    background: var(--backdrop);
    font-family: "Montserrat", Arial, sans-serif;
  }
  .letterhead {
    position: absolute; left: 300px; top: 27px;
    width: 600px; height: 820px;
    background: var(--paper);
    box-shadow: 0 6px 18px rgba(0,0,0,0.12);
    overflow: hidden;
  }
  .header-swoosh { position: absolute; left: 0; top: 0; width: 600px; height: 130px; }
  .office-contact {
    position: absolute; right: 40px; top: 14px;
    color: #fff; font-size: 9px; line-height: 12.5px; text-align: right;
  }
  .office-contact .icon { display: inline-block; width: 9px; height: 8px; margin-left: 3px; vertical-align: -1px; }
  .firm-name {
    position: absolute; left: 50px; top: 116px;
    color: var(--navy); font-size: 21px; font-weight: 600; letter-spacing: 0.5px;
  }
  .recipient {
    position: absolute; left: 48px; top: 210px;
    font-size: 9px; line-height: 13px; color: var(--ink);
  }
  .letter-body {
    position: absolute; left: 48px; right: 44px; top: 278px;
    font-size: 8.6px; line-height: 14px; color: var(--ink);
  }
  .letter-body p { margin-bottom: 22px; }
  .closing { position: absolute; left: 48px; top: 566px; font-size: 9px; color: var(--ink); }
  .signature { position: absolute; left: 44px; top: 584px; width: 150px; height: 48px; border-radius: 4px;
    background: linear-gradient(90deg, var(--sign-tone), #f6f6f7); }
  .footer-bar { position: absolute; left: 0; bottom: 0; width: 600px; height: 8px; display: flex; }
  .footer-bar .navy { flex: 0 0 36%; background: var(--navy); }
  .footer-bar .red { flex: 0 0 33%; background: linear-gradient(90deg, var(--red-deep), var(--red)); }
  .footer-bar .blue { flex: 0 0 3%; background: var(--blue); }
  .footer-bar .plum { flex: 1; background: linear-gradient(90deg, var(--blue), var(--plum)); }
</style>
</head>
<body>
<main class="letterhead">
  <svg class="header-swoosh" viewBox="0 0 600 130" aria-hidden="true">
    <defs>
      <linearGradient id="redSweep" x1="0" y1="0" x2="1" y2="0">
        <stop offset="0" stop-color="#8e1519"/>
        <stop offset="1" stop-color="#e1232b"/>
      </linearGradient>
    </defs>
    <path d="M0 0 H600 V44 C597 86 530 94 450 98 C300 104 120 98 0 66 Z" fill="var(--navy)"/>
    <path d="M505 103 C380 110 150 106 0 70 L0 98 C140 122 370 120 505 103 Z" fill="url(#redSweep)"/>
  </svg>

  <address class="office-contact" style="font-style:normal">
    1475 Calloway Street<br>
    Suite 210, Houston, Texas 77041<br>
    832-361-9027<svg class="icon" viewBox="0 0 10 9" aria-label="phone"><path d="M1 3 C1 1 9 1 9 3 L7 4 L6 3 H4 L3 4 Z M2 5 H8 V8 H2 Z" fill="#fff"/></svg><br>
    832-614-7359<svg class="icon" viewBox="0 0 10 9" aria-label="fax"><path d="M3 0 H7 V3 H3 Z M1 3 H9 V7 H1 Z M3 6 H7 V9 H3 Z" fill="#fff"/></svg>
  </address>

  <div class="firm-name">Marwick Law</div>

  <div class="recipient">
    Mr/s<br>First Name and Last Name<br>Company Name<br>Address
  </div>

  <div class="letter-body">
    <p>Lorem Ipsum is simply dummy text of the printing and typesetting industry. Lorem Ipsum has been the industry's standard dummy text ever since the 1500s, when an unknown printer took a galley of type and scrambled it to make a type specimen book. It has survived not only five centuries, but also the leap into electronic typesetting, remaining essentially unchanged. It was popularised in the 1960s with the release of Letraset sheets containing Lorem Ipsum passages.</p>
    <p>he standard chunk of Lorem Ipsum used since the 1500s is reproduced below for those interested. Sections 1.10.32 and 1.10.33 from "de Finibus Bonorum et Malorum" by Cicero are also reproduced in their exact original form, accompanied by English versions from the 1914 translation by H. Rackham. Lorem ipsum dolor sit amet, consectetur adipiscing elit, sed do eiusmod tempor incididunt ut labore et dolore magna aliqua.</p>
    <p>It is a long established fact that a reader will be distracted by the readable content of a page when looking at its layout. The point of using Lorem Ipsum is that it has a more-or-less normal distribution of letters, as opposed to using 'Content here, content here', making it look like readable English. Many desktop publishing packages and web page editors now .</p>
  </div>

  <div class="closing">Your Sincerely,</div>
  <div class="signature" role="img" aria-label="Handwritten signature"></div>

  <div class="footer-bar" aria-hidden="true">
    <span class="navy"></span><span class="red"></span><span class="blue"></span><span class="plum"></span>
  </div>
</main>
</body>
</html>
```